Pull Up Banner - Recruitment Company

We would like a design for a pull up banner.

For context: we are a recruitment business. We specialise in helping people in healthcare industry to find jobs in Australia.

I have come up with several ideas and text for the banner. Feel free to use the following as you see appropriate:

- Our logo (see attached)
- 'Healthcare Recruitment Agency'
- Some sort of imagine / cartoon of medical professionals (ie. doctor, nurse, physiotherapist, speech pathologist). A cartoon is more friendly than committing to a photo
- 'Empowering your next career move'
- 'Discover tailored opportunities based on your career preferences'
- Dot points (allied health, nursing, medical imaging)
- Contact info at the bottom including our website (www.quellastaffing.com.au, our Instagram handle @quellastaffing, Mobile: XXXX XXX XXX. The title section for contact information could be 'Get in touch:'

Feel free to submit a couple of designs and we can merge aspects that look good on your designs and find the perfect fit.
Thank you
Updates

Hello,

Thank you for your initial submissions to this project. I appreciate the time you've invested.

After reviewing the first attempt, I'd like to share some feedback and initial observations:

- Professionalism and engagement: Is the overall appearance of the banner professional? It's crucial that we have a high-quality design as this will represent our business.

- Image selection: The image (whether cartoon or real people) appears quite generic. Please consider submitting the banner with a few different photos in the middle for us to choose from. Ensure the image is a good fit and not simply a generic stock photo.

- Contact section: Kindly remove the phone number; we no longer wish to include it on the banner. Instead, please include our website (www.quellastaffing.com.au) and Instagram handle (@quellastaffing).

- Color scheme: White, black, and red/pink are preferred, or alternatively, blue. However, please avoid incorporating too many different colors as it may detract from the professional appearance.

We will be printing the design on a banner and require it to look professional and engaging.

Thank you once again for your submissions. I hope the feedback provided above is helpful.

Warm regards,

Target Market(s)

Allied Health Australia

Font styles to use
Serif

Colors
0054AA
0677BA
7BADD7
CADEEF
E8F1F8
0094D4
00A9DD
6FCCEA
C7EBF8
E9F6FB
EB3D1F
EC4F4E
F09395
F8D3D4
FCEDEE

```html
<!DOCTYPE html>
<html lang="en">
<head>
<meta charset="utf-8">
<title>Quella Staffing – Healthcare Recruitment Agency Banner</title>
<link rel="stylesheet" href="https://fonts.googleapis.com/css2?family=Poppins:wght@300;400;500;600;700;800&display=swap">
<style>
  :root {
    --navy: #32486b;
    --navy-deep: #18223a;
    --sky: #7fb0f5;
    --mist: #aab6cf;
    --white: #ffffff;
    --ring: #5c74a8;
    --blob-light: #eef2fb;
    --blob-mid: #b9c8e8;
  }
  * { margin: 0; padding: 0; box-sizing: border-box; }
  html, body { width: 672px; height: 1200px; overflow: hidden; }
  body {
    font-family: "Poppins", sans-serif;
    background: var(--navy);
    color: var(--white);
  }
  .banner { position: relative; width: 672px; height: 1200px; overflow: hidden; background: var(--navy); }

  .brand { position: absolute; left: 74px; top: 52px; }
  .brand-name { font-size: 40px; font-weight: 700; letter-spacing: 1px; line-height: 1; color: var(--white); }
  .brand-rule { display: block; width: 160px; height: 9px; background: var(--white); margin-top: 10px; }

  .headline { position: absolute; left: 70px; top: 150px; line-height: 0.92; }
  .headline span { display: block; font-size: 70px; letter-spacing: -0.5px; }
  .headline .h-sky { color: var(--sky); font-weight: 800; }
  .headline .h-white { color: var(--white); font-weight: 800; }
  .headline .h-mist { color: var(--mist); font-weight: 400; }

  .hero { position: absolute; left: 40px; top: 330px; width: 600px; height: 400px; }

  .tagline { position: absolute; left: 0; width: 672px; top: 740px; text-align: center; font-weight: 700; font-size: 31px; line-height: 1.05; }
  .tagline .accent { display: block; color: var(--sky); }
  .intro { position: absolute; left: 0; width: 672px; top: 820px; text-align: center; font-size: 23px; font-weight: 400; line-height: 1.25; }

  .base-wave { position: absolute; left: 0; top: 0; width: 672px; height: 1200px; }

  .specialties { position: absolute; top: 890px; left: 0; width: 672px; display: flex; justify-content: space-between; padding: 0 55px; }
  .specialty { width: 170px; text-align: center; }
  .specialty svg { display: block; margin: 0 auto; }
  .specialty-label { font-size: 23px; font-weight: 500; line-height: 1.05; margin-top: 4px; height: 50px; display: flex; align-items: center; justify-content: center; }

  .handle { position: absolute; top: 1075px; left: 50%; transform: translateX(-50%); background: var(--sky); color: var(--navy-deep); border-radius: 18px; padding: 3px 20px; font-size: 20px; font-weight: 600; letter-spacing: 1px; display: flex; align-items: center; gap: 8px; white-space: nowrap; }
  .handle-dot { width: 18px; height: 18px; border-radius: 4px; background: var(--white); }

  .website { position: absolute; top: 1130px; left: 0; width: 672px; text-align: center; font-size: 25px; letter-spacing: 3px; font-weight: 300; }
  .website b { font-weight: 600; }
</style>
</head>
<body>
<main class="banner">
  <svg class="base-wave" viewBox="0 0 672 1200" aria-hidden="true">
    <path d="M0 930 C120 905 230 885 336 900 C460 918 590 900 672 810 L672 1200 L0 1200 Z" fill="var(--navy-deep)"/>
  </svg>

  <header class="brand">
    <div class="brand-name">Quella Staffing</div>
    <span class="brand-rule"></span>
  </header>

  <h1 class="headline">
    <span class="h-sky">HEALTHCARE</span>
    <span class="h-white">RECRUITMENT</span>
    <span class="h-mist">AGENCY</span>
  </h1>

  <svg class="hero" viewBox="0 0 600 400" role="img" aria-label="Illustration of a doctor beside a patient in a medical scanner">
    <defs>
      <radialGradient id="heroFill" cx="0.5" cy="0.5" r="0.6">
        <stop offset="0" stop-color="var(--blob-light)"/>
        <stop offset="1" stop-color="var(--blob-mid)"/>
      </radialGradient>
    </defs>
    <circle cx="150" cy="120" r="110" fill="var(--navy-deep)"/>
    <path d="M370 10 C470 -5 580 70 580 190 C580 320 470 400 330 395 C200 392 70 350 40 260 C20 190 70 140 110 130 C160 118 200 80 250 50 C290 25 320 15 370 10 Z" fill="var(--ring)"/>
    <path d="M370 25 C460 15 555 80 555 190 C555 310 460 380 330 378 C210 376 85 340 60 260 C45 200 85 155 120 148 C170 135 205 100 255 68 C295 42 330 30 370 25 Z" fill="url(#heroFill)"/>
  </svg>

  <h2 class="tagline">EMPOWERING YOUR NEXT<span class="accent">CAREER MOVE</span></h2>
  <p class="intro">Discover tailored opportunities based on<br>your career preferences</p>

  <section class="specialties">
    <div class="specialty">
      <svg width="110" height="100" viewBox="0 0 110 100" aria-hidden="true">
        <path d="M10 55 A45 45 0 0 1 100 55" fill="none" stroke="var(--sky)" stroke-width="3"/>
        <circle cx="55" cy="55" r="38" fill="var(--white)"/>
        <path d="M55 72 C35 58 36 42 46 40 C51 39 54 42 55 45 C56 42 59 39 64 40 C74 42 75 58 55 72 Z" fill="var(--navy-deep)"/>
      </svg>
      <div class="specialty-label">Allied<br>health</div>
    </div>
    <div class="specialty">
      <svg width="110" height="100" viewBox="0 0 110 100" aria-hidden="true">
        <path d="M10 55 A45 45 0 0 1 100 55" fill="none" stroke="var(--sky)" stroke-width="3"/>
        <circle cx="55" cy="55" r="38" fill="var(--white)"/>
        <rect x="49" y="36" width="12" height="38" rx="2" fill="var(--navy-deep)"/>
        <rect x="36" y="49" width="38" height="12" rx="2" fill="var(--navy-deep)"/>
      </svg>
      <div class="specialty-label">Nursing</div>
    </div>
    <div class="specialty">
      <svg width="110" height="100" viewBox="0 0 110 100" aria-hidden="true">
        <path d="M10 55 A45 45 0 0 1 100 55" fill="none" stroke="var(--sky)" stroke-width="3"/>
        <circle cx="55" cy="55" r="38" fill="var(--white)"/>
        <rect x="35" y="38" width="40" height="30" rx="4" fill="none" stroke="var(--navy-deep)" stroke-width="4"/>
        <path d="M39 56 L48 56 L52 46 L58 64 L62 56 L71 56" fill="none" stroke="var(--navy-deep)" stroke-width="3" stroke-linejoin="round"/>
      </svg>
      <div class="specialty-label">Medical<br>imaging</div>
    </div>
  </section>

  <div class="handle"><span class="handle-dot"></span>@quellastaffing</div>

  <p class="website">www.<b>quellastaffing</b>.com.au</p>
</main>
</body>
</html>
```